New Business Card

Need new business cards like attached. if possible add QR code. Vertical Business Card

I need creative and unique business card design using my company logo. Ok to change logo color. We are a small brokerage doing both Real Estate and Mortgage services. Need to have the follow on business card;
1. agent name - Nola Brenner - Realtor
2. cell - 555-555-2146
3. license number - DRE 07461392
4. business name - Tallow Ridge Realty & Lending, Inc
5. business office - 555-555-4817
6. business address - 482 W. Larkmoor Ave #212, Fernhollow CA 90000
7. business logo - attached (ok to use different color on logo)

```html
<!DOCTYPE html>
<html lang="en">
<head>
<meta charset="utf-8">
<title>Tallow Ridge Realty &amp; Lending — Business Card</title>
<link href="https://fonts.googleapis.com/css2?family=Arimo:wght@400;700&display=swap" rel="stylesheet">
<style>
  :root {
    --bg: #2a2a2c;
    --card: #1c1d1f;
    --card-back-top: #2e2f31;
    --card-back-bottom: #121314;
    --blue: #14a9f0;
    --blue-deep: #0a78e8;
    --white: #f2f2f2;
    --rule: #cfcfcf;
  }
  * { margin: 0; padding: 0; box-sizing: border-box; }
  html, body { width: 1200px; height: 1108px; overflow: hidden; }
  body {
    background: var(--bg);
    font-family: "Arimo", Arial, sans-serif;
    display: flex;
    align-items: center;
    justify-content: center;
    gap: 80px;
  }
  .card {
    width: 440px;
    height: 770px;
    border-radius: 26px;
    position: relative;
    overflow: hidden;
  }
  .card--front {
    background: var(--card);
    display: flex;
    flex-direction: column;
    align-items: center;
    padding-top: 80px;
    color: var(--white);
    text-align: center;
  }
  .brand {
    display: flex;
    flex-direction: column;
    align-items: center;
    gap: 18px;
    text-align: center;
  }
  .brand__mark {
    width: 110px; height: 110px;
    background: linear-gradient(135deg, var(--blue), var(--blue-deep));
  }
  .brand__name {
    color: var(--blue);
    font-weight: 400;
    text-transform: uppercase;
    display: flex;
    flex-direction: column;
    align-items: center;
    gap: 6px;
  }
  .brand__name-main { font-size: 24px; letter-spacing: 7px; }
  .brand__name-sub { font-size: 14px; letter-spacing: 4px; }
  .agent__name {
    margin-top: 46px;
    color: var(--blue);
    font-weight: 700;
    font-size: 34px;
    text-transform: uppercase;
  }
  .agent__title { font-size: 26px; margin-top: 4px; }
  .contact-divider {
    display: flex; align-items: center; gap: 14px;
    width: 360px; margin-top: 22px;
  }
  .contact-divider .rule { flex: 1; }
  .icon {
    width: 40px; height: 40px; border-radius: 8px;
    background: linear-gradient(135deg, var(--blue), var(--blue-deep));
    display: flex; align-items: center; justify-content: center;
  }
  .rule { height: 1px; background: var(--rule); }
  .phones { font-size: 27px; line-height: 1.35; margin-top: 12px; }
  .section-rule { width: 360px; margin: 18px 0; }
  .address { font-size: 27px; line-height: 1.3; }
  .license { font-size: 27px; }
  .license__tag { color: var(--blue); font-weight: 700; }

  .card--back {
    background: linear-gradient(180deg, var(--card-back-top), var(--card-back-bottom));
    display: flex; align-items: center; justify-content: center;
  }
  .back__pattern { position: absolute; inset: 0; }
  .card--back .brand { position: relative; }
  .card--back .brand__mark { width: 96px; height: 96px; }
</style>
</head>
<body>
  <section class="card card--front">
    <div class="brand">
      <div class="brand__mark"></div>
      <div class="brand__name">
        <span class="brand__name-main">Tallow Ridge</span>
        <span class="brand__name-sub">Realty &amp; Lending, Inc</span>
      </div>
    </div>
    <h1 class="agent__name">Nola Brenner</h1>
    <p class="agent__title">Realtor</p>
    <div class="contact-divider">
      <div class="rule"></div>
      <span class="icon">
        <svg width="24" height="24" viewBox="0 0 24 24" fill="none" stroke="#0b1f33" stroke-width="2"><path d="M6 3l3 4-2 2c1 3 3 5 6 6l2-2 4 3-2 4C10 20 4 14 3 6z"/></svg>
      </span>
      <span class="icon">
        <svg width="24" height="24" viewBox="0 0 24 24" fill="none" stroke="#0b1f33" stroke-width="2"><rect x="7" y="2" width="10" height="20" rx="2"/><line x1="11" y1="18" x2="13" y2="18"/></svg>
      </span>
      <div class="rule"></div>
    </div>
    <p class="phones">555-555-2146<br>555-555-4817</p>
    <div class="rule section-rule"></div>
    <p class="address">482 W. Larkmoor Ave #212<br>Fernhollow CA 90000</p>
    <div class="rule section-rule"></div>
    <p class="license"><span class="license__tag">LIC</span> DRE 07461392</p>
  </section>

  <section class="card card--back">
    <div class="back__pattern" role="img" aria-label="Embossed grid of repeated brand marks in dark grey"></div>
    <div class="brand">
      <div class="brand__mark"></div>
      <div class="brand__name">
        <span class="brand__name-main">Tallow Ridge</span>
        <span class="brand__name-sub">Realty &amp; Lending, Inc</span>
      </div>
    </div>
  </section>
</body>
</html>
```